Corvane Paintless Dent Removal

Our company works on vehicles removing dents using a highly skilled trade which the metal is massaged out with special tools without disturbing the original paint, hence paintless dent removal. Besides keeping the paint and metal original its also very environmentally friendly since no paint or toxic fillers are used. Also we we are one of the most experienced companies in the business with 25 years

Target Market(s)

Retail Automobile consumers, Auto Dealerships and Auto Body Shops

Industry/Entity Type

Auto Repair

Contact Information for Business Card

Dale Hollister
PO Box 518 Brookmere, NY 11962
631-555-0148
corvanepdr@mailbox-example.com
website corvanepdr.example
youtube corvane paintless dent removal
25 years of experience removing Dents, Dings and Hail Damage

Font styles to use
Serif
Sans Serif

Colors

Designer to choose colors to be used in the design.

Requirements
Must have
• I do like things that are simple but classy and somewhat bold, also I like my logo so that should be somewhat important

```html
<!DOCTYPE html>
<html lang="en">
<head>
<meta charset="utf-8">
<title>Corvane Paintless Dent Removal – Business Card</title>
<link rel="stylesheet" href="https://fonts.googleapis.com/css2?family=Roboto:wght@400;700&family=Roboto+Condensed:wght@700&display=swap">
<style>
  :root {
    --navy: #14284f;
    --green: #7dc412;
    --card-white: #f7f7f7;
    --text-gray: #555a60;
    --divider: #c9c9c9;
    --backdrop: #e6e4e0;
    --badge-dark: #1b1b1b;
    --badge-gold: #d9a637;
    --white: #ffffff;
  }
  * { margin: 0; padding: 0; box-sizing: border-box; }
  html, body { width: 1200px; height: 960px; overflow: hidden; }
  body {
    background: var(--backdrop);
    position: relative;
    font-family: "Roboto", Arial, sans-serif;
  }
  .card {
    position: absolute;
    width: 600px;
    height: 342px;
    box-shadow: 0 3px 8px rgba(0,0,0,0.25);
    overflow: hidden;
  }
  .card-front { left: 314px; top: 113px; background: var(--card-white); }
  .card-back { left: 311px; top: 472px; background: var(--green); }

  .wordmark {
    position: absolute;
    font-family: "Roboto", Arial, sans-serif;
    font-weight: 700;
    color: var(--navy);
    text-align: center;
    line-height: 1;
  }
  .wordmark .brand { display: block; font-size: 38px; letter-spacing: 1px; }
  .wordmark .trade { display: block; font-size: 15px; margin-top: 4px; }
  .card-front .wordmark { left: 40px; top: 150px; width: 242px; }
  .card-back .wordmark { left: 160px; top: 138px; width: 280px; }
  .card-back .wordmark .brand { font-size: 42px; }
  .card-back .wordmark .trade { font-size: 16px; }

  .experience-seal {
    position: absolute;
    left: 503px; top: 19px;
    width: 70px; height: 70px;
  }
  .divider {
    position: absolute;
    left: 308px; top: 97px;
    width: 1px; height: 152px;
    background: var(--divider);
  }
  .contact { position: absolute; left: 332px; top: 94px; }
  .contact-name {
    font-family: "Roboto Condensed", Arial, sans-serif;
    font-weight: 700;
    font-size: 21px;
    color: var(--navy);
    letter-spacing: 0.3px;
    margin-bottom: 10px;
  }
  .contact-address { font-size: 14px; color: var(--text-gray); line-height: 19px; margin-bottom: 8px; }
  .contact-list { list-style: none; }
  .contact-list li {
    font-size: 14px; color: var(--text-gray);
    line-height: 19px; display: flex; align-items: center;
  }
  .contact-list svg { width: 13px; height: 13px; margin-right: 10px; flex: none; }

  .footer-band { position: absolute; left: 0; bottom: 0; width: 600px; height: 17px; }

  .card-back .site {
    position: absolute;
    left: 0; top: 281px; width: 600px;
    text-align: center;
    font-size: 14px;
    letter-spacing: 5.5px;
    color: var(--white);
  }
</style>
</head>
<body>

<section class="card card-front" aria-label="Business card front">
  <div class="wordmark">
    <span class="brand">CORVANE</span>
    <span class="trade">Paintless Dent Removal</span>
  </div>

  <svg class="experience-seal" viewBox="0 0 70 70" role="img" aria-label="25 years of experience seal">
    <circle cx="35" cy="35" r="34" fill="var(--badge-gold)"/>
    <circle cx="35" cy="35" r="30" fill="var(--badge-dark)"/>
  </svg>

  <div class="divider"></div>

  <div class="contact">
    <h1 class="contact-name">DALE HOLLISTER</h1>
    <p class="contact-address">PO Box 518<br>Brookmere, NY 11962</p>
    <ul class="contact-list">
      <li>
        <svg viewBox="0 0 24 24" aria-hidden="true"><path fill="var(--navy)" d="M6.6 10.8a15.1 15.1 0 0 0 6.6 6.6l2.2-2.2c.3-.3.7-.4 1-.2 1.1.4 2.3.6 3.6.6.6 0 1 .4 1 1V20c0 .6-.4 1-1 1A17 17 0 0 1 3 4c0-.6.4-1 1-1h3.5c.6 0 1 .4 1 1 0 1.3.2 2.5.6 3.6.1.3 0 .7-.2 1z"/></svg>
        631-555-0148
      </li>
      <li>
        <svg viewBox="0 0 24 24" aria-hidden="true"><rect x="2" y="5" width="20" height="14" rx="1" fill="var(--navy)"/><path d="M3 6l9 7 9-7" fill="none" stroke="var(--card-white)" stroke-width="1.8"/></svg>
        corvanepdr@mailbox-example.com
      </li>
      <li>
        <svg viewBox="0 0 24 24" aria-hidden="true"><circle cx="12" cy="12" r="10" fill="none" stroke="var(--navy)" stroke-width="2.4"/><ellipse cx="12" cy="12" rx="4" ry="10" fill="none" stroke="var(--navy)" stroke-width="2"/><path d="M2 12h20" stroke="var(--navy)" stroke-width="2"/></svg>
        corvanepdr.example
      </li>
      <li>
        <svg viewBox="0 0 24 24" aria-hidden="true"><rect x="3" y="5" width="18" height="14" rx="2" fill="var(--navy)"/></svg>
        corvane paintless dent removal
      </li>
    </ul>
  </div>

  <svg class="footer-band" viewBox="0 0 600 17" preserveAspectRatio="none" aria-hidden="true">
    <polygon points="0,0 393,0 389,17 0,17" fill="var(--navy)"/>
    <polygon points="395,0 600,0 600,17 391,17" fill="var(--white)"/>
    <polygon points="399,0 600,0 600,17 395,17" fill="var(--green)"/>
  </svg>
</section>

<section class="card card-back" aria-label="Business card back">
  <div class="wordmark">
    <span class="brand">CORVANE</span>
    <span class="trade">Paintless Dent Removal</span>
  </div>
  <p class="site">www.corvanepdr.example</p>
</section>

</body>
</html>
```